A-Stand Directional Sign Design

Objective:
We need a professional graphic design for an A-Stand sign that will guide customers arriving in our parking lot to our office. The design should be visually clear, welcoming, and aligned with our brand identity.
REQUIREMENTS:
Two versions of the design:
- One with an arrow pointing left
- One with an arrow pointing right
(This allows us to place the A-Stand anywhere and flip the graphic as needed.)
DIMENSIONS:
- Viewable Area: 30" x 40"
BRAND ALIGNMENT:
- Colors, fonts, and overall style should match our website: www.glidemarrow.com
- Clean, modern, and professional look consistent with our aviation/tourism brand
CONTENT:
- Clear directional arrow (left or right depending on version)
- Text: “Office Entrance” or similar concise wording (designers may propose alternatives if they improve clarity)
READABILITY:
- Bold, high-contrast design for visibility from a distance
- Simple layout that avoids clutter
DELIVERABLES:
- Final artwork in print-ready format (PDF preferred)
- Two versions: Arrow Left and Arrow Right
DESIGN GOAL:
Ensure customers can easily find our office upon arrival, while reinforcing glideMARROW’s professional and welcoming brand image.
Target Market(s)
Tourism
Look and feel

```html
<!DOCTYPE html>
<html lang="en">
<head>
<meta charset="utf-8">
<title>glideMARROW – Office Entrance A-Stand</title>
<link href="https://fonts.googleapis.com/css2?family=Montserrat:wght@600;800&display=swap" rel="stylesheet">
<style>
  :root {
    --page-bg: #e8ecf1;
    --sign-white: #f5f6f7;
    --brand-blue: #2470b0;
    --sky-light: #b6cbe0;
    --sky-mid: #8fabc8;
    --tarmac: #7890a8;
    --text-white: #ffffff;
  }
  html, body {
    margin: 0;
    padding: 0;
    width: 1200px;
    height: 1072px;
    overflow: hidden;
    background: var(--page-bg);
    font-family: "Montserrat", Arial, sans-serif;
  }
  .sign {
    position: absolute;
    left: 240px;
    top: 56px;
    width: 720px;
    height: 960px;
    background: var(--sign-white);
    box-shadow: 0 10px 30px rgba(30, 50, 80, 0.18);
    overflow: hidden;
  }
  .sign__header {
    position: absolute;
    left: 0;
    top: 0;
    width: 100%;
    height: 440px;
  }
  .brand {
    position: absolute;
    top: 92px;
    left: 0;
    width: 100%;
    display: flex;
    align-items: center;
    justify-content: center;
    gap: 12px;
  }
  .brand__dot {
    width: 22px;
    height: 22px;
    border-radius: 50%;
    background: var(--brand-blue);
  }
  .brand__name {
    font-weight: 600;
    font-size: 34px;
    color: var(--brand-blue);
    letter-spacing: 0.5px;
  }
  .direction-arrow {
    position: absolute;
    left: 100px;
    top: 220px;
    width: 520px;
    height: 220px;
  }
  .sign__photo {
    position: absolute;
    left: 0;
    top: 460px;
    width: 100%;
    height: 500px;
    background: linear-gradient(180deg, var(--sky-light) 0%, var(--sky-mid) 55%, var(--tarmac) 100%);
  }
  .entrance-title {
    position: absolute;
    left: 0;
    top: 640px;
    width: 100%;
    margin: 0;
    text-align: center;
    font-weight: 800;
    font-size: 96px;
    line-height: 1.02;
    color: var(--text-white);
    letter-spacing: 2px;
    text-shadow: 0 2px 8px rgba(20, 40, 70, 0.25);
  }
</style>
</head>
<body>
  <main class="sign">
    <section class="sign__header">
      <div class="brand">
        <span class="brand__dot"></span>
        <span class="brand__name">glideMARROW.com</span>
      </div>
      <svg class="direction-arrow" viewBox="0 0 520 220" aria-label="Arrow pointing right">
        <rect x="6" y="70" width="330" height="84" rx="28" fill="var(--brand-blue)"/>
        <path d="M300 14 L506 112 L300 208 Z" fill="var(--brand-blue)" stroke="var(--brand-blue)" stroke-width="26" stroke-linejoin="round"/>
      </svg>
    </section>
    <div class="sign__photo" role="img" aria-label="Photo of a small helicopter parked on a wet tarmac under a cloudy blue sky"></div>
    <h1 class="entrance-title">OFFICE<br>ENTRANCE</h1>
  </main>
</body>
</html>
```